Printed Circuit Board Company Web Site Design - Please see new file 82012 web design

We are a printed circuit board manufacturer. Need a company professional web site to allow our potential customers to know more about our background, capability and our products. The web site will contain three languages, which are Chinese, English and Japanese. Our audience are mainly electronic companies that procure printed circuit boards. I have a word document that have all the required text in all three languages. The final design should communicate the impression that we embrace quality, trustworthiness and long term partnership business principles.
We should have sections that allow us to post pictures of our facilities.
I have added the three files in three different languages.
Some of the information is below:
Background
RDV Harbourline Limited (RDV) was set up in Hong Kong in 2007 by two Hong Kong entrepreneurs, Mr. Tak Wong and Mr. Lok Fai. We acquired the single sided printed circuit board factory located in Dongguan City, Guangdong Province, China, from Tovand Corporation of the U.S. in 2007. In addition to RDV, Mr. Wong and Mr. Fai also own Halberd Technology Company Limited, a semiconductor company based in Hong Kong since 1997 with a total investment of over US$100 million. Halberd is engaged in the manufacturing of flexible substrates and MEMS assembly business.
RDV has been awarded TS 16949 and ISO14000 certificates since 2009 and 2004 respectively.
Business Principles
RDV Harbourline Limited strives to be a professional top notched printed circuit board supplier. We embrace four “EXCELLENCE” principles, namely, excellence in quality, excellence in prices, excellence in services and excellence in on time delivery.
We approach each customer with a long-term partnership view that delivers the lowest ownership costs and highest total values to our customers. We customize quotations and solutions in order to allow our customers to win more businesses. We believe by thinking from our customers’ points of view we will be able to create a WIN-WIN relationship.
Customers
Due to our excellent quality, services and production systems, RDV Harbourline Limited manage to service a number of large Japanese and US customers, which include:
Technical capability overview
Below is an overview of our current capability:
Target Market(s)
Electronic companies buyers
Industry/Entity Type
Business
Requirements
Must have
- Capability description
Should not have
- no cartoon

```html
<!DOCTYPE html>
<html lang="en">
<head>
<meta charset="utf-8">
<title>RDV Harbourline Limited</title>
<link href="https://fonts.googleapis.com/css2?family=Arimo:ital,wght@0,400;0,700;1,700&display=swap" rel="stylesheet">
<style>
:root{
  --green-deep:#0c3029;
  --green-dark:#123d34;
  --green-mid:#1d6b52;
  --green-brand:#1a7a50;
  --green-head:#0f5a3c;
  --teal-tab:#2e7a68;
  --orange:#f08a0c;
  --orange-dark:#d26f00;
  --ink:#222;
  --muted:#555;
  --rule:#d9d9d9;
  --grid:#eef0ef;
  --white:#fff;
}
*{margin:0;padding:0;box-sizing:border-box}
html,body{width:667px;height:1200px;overflow:hidden}
body{font-family:"Arimo",Arial,sans-serif;color:var(--ink);background:var(--white);position:relative;font-size:7.5px;line-height:1.45}
.abs{position:absolute}
a{color:inherit;text-decoration:none}

/* top bar */
.topbar{left:0;top:0;width:667px;height:20px;background:#f7f7f7;border-bottom:1px solid #e2e2e2}
.lang{left:56px;top:5px;font-size:7px;font-weight:700;color:#333;display:flex;align-items:center;gap:4px}
.lang .flag{width:11px;height:7px;background:linear-gradient(#b22 0 50%,#35a 50%)}
.nav{left:353px;top:3px;display:flex}
.nav a{font-size:8px;font-weight:700;color:var(--green-deep);padding:3px 7px;text-transform:uppercase;letter-spacing:.2px}
.nav a.active{background:var(--teal-tab);color:var(--white);border-radius:3px;padding:3px 10px;margin-right:6px}

/* header */
.header{left:0;top:20px;width:667px;height:67px;background:linear-gradient(#fff,#f2f2f2)}
.logo{left:54px;top:33px;width:128px;color:var(--green-brand);font-weight:700;line-height:1}
.logo .big{font-size:30px;letter-spacing:6px;display:block}
.logo .small{font-size:10px;display:block;text-align:center;margin-top:2px}
.login{left:504px;top:34px;width:107px;height:18px;background:linear-gradient(#2f8a6d,#1b5d49);border-radius:3px;color:var(--white);font-size:8.5px;font-weight:700;display:flex;align-items:center;justify-content:center;gap:5px}
.mail{left:521px;top:70px;font-size:8px;font-weight:700;color:var(--green-head);display:flex;align-items:center;gap:4px}

/* hero */
.hero{left:0;top:87px;width:667px;height:223px;background:radial-gradient(ellipse at 40% 30%,#1c4a40,var(--green-deep) 70%)}
.hero-title{left:56px;top:102px;width:290px;font-size:17.5px;font-weight:400;line-height:1.2;color:var(--white)}
.hero-text{left:56px;top:212px;width:290px;font-size:7.6px;color:#e6efec;font-weight:700;line-height:1.5}
.btn{background:linear-gradient(var(--orange),var(--orange-dark));color:var(--white);font-size:8px;font-weight:700;border-radius:3px;display:flex;align-items:center;justify-content:center;text-transform:uppercase}
.hero-btn{left:56px;top:260px;width:71px;height:16px}
.hero-photo{left:357px;top:107px;width:254px;height:167px;border:4px solid var(--white);background:linear-gradient(135deg,#c7cfd0,#8d9c9a 55%,#5d6f6c)}
.slider-tab{left:297px;top:291px;width:73px;height:19px}

/* principles */
.section-title{font-size:10px;font-weight:700;font-style:italic;color:var(--green-head);text-transform:uppercase}
.principles-title{left:56px;top:324px}
.principle{top:356px;display:flex;align-items:center;gap:7px;color:var(--green-head);font-size:10px;line-height:1.1}
.principle .num{width:40px;height:40px;border-radius:50%;background:radial-gradient(circle at 40% 35%,#2d8a6c,#0e4a39);border:2px solid #cfd8d4;color:var(--white);font-size:19px;font-weight:700;display:flex;align-items:center;justify-content:center}
.divider{left:0;width:667px;height:12px;background:linear-gradient(#ececec,#fff)}

/* about */
.about-title{left:56px;top:435px}
.about-photo{left:56px;top:459px;width:107px;height:72px;background:linear-gradient(135deg,#e9eceb,#b9c2c0)}
.about-text{left:168px;top:458px;width:262px;font-size:6.8px;color:#333}
.about-text.full{left:56px;top:536px;width:380px}
.about-text b{color:var(--green-head);text-decoration:underline}
.about-btn{left:56px;top:557px;width:70px;height:16px}
.updates-title{left:451px;top:435px}
.tweet{left:451px;width:165px;display:flex;gap:6px;font-size:6.8px;color:#333}
.tweet .avatar{flex:none;width:27px;height:27px;background:linear-gradient(#d4d9d8,#98a4a2);border:1px solid #ccc}
.tweet .by{color:var(--green-brand);font-weight:700;font-style:italic}
.badge{left:578px;top:545px;width:32px;height:26px;border-radius:50%;background:#5fb7d9}

/* products & services */
.band-title{height:13px;display:flex;align-items:center}
.band-title span{background:var(--white);padding-right:8px}
.band-title::after{content:"";flex:1;height:9px;background:linear-gradient(90deg,#ddd,#eee)}
.products-title{left:56px;top:590px;width:270px}
.services-title{left:347px;top:590px;width:264px}
.prod-h{left:56px;width:270px;font-size:8.8px;color:var(--green-head);text-transform:uppercase;line-height:1.3}
.prod-p{left:56px;width:270px;font-size:6.8px;color:#333}
.more{font-weight:700;color:var(--green-head)}
.dash{left:56px;top:709px;width:270px;border-top:1px dashed #bbb}
.svc-photo{left:347px;top:622px;width:98px;height:67px;background:linear-gradient(135deg,#eef1f0,#b4bfbd)}
.svc-text{left:451px;width:160px;font-size:6.8px;color:#333}
.svc-text.wide{left:347px;width:264px}

/* customers */
.customers{left:0;top:827px;width:667px;height:187px;background-color:#f6f7f6;background-image:linear-gradient(var(--grid) 1px,transparent 1px),linear-gradient(90deg,var(--grid) 1px,transparent 1px);background-size:12px 12px}
.customers-title{left:56px;top:840px}
.cat{font-size:7.5px;font-weight:700;color:var(--green-head)}
.cat-rule{border-bottom:1px solid #bbb;padding-bottom:1px}
.brands{display:flex;gap:16px;align-items:center;font-size:9px;font-weight:700;color:#333}
.brands i{display:inline-block;width:6px;height:6px;background:#333;margin-right:3px;vertical-align:middle}

/* footer */
.footer{left:0;top:1014px;width:667px;height:186px;background:radial-gradient(ellipse at 50% 40%,#173f36,#0a2621 75%)}
.fcol{top:1030px;color:#dfe8e5;font-size:6.6px;line-height:1.65}
.fcol h4{font-size:7px;font-weight:700;color:var(--white);text-transform:uppercase;margin-bottom:5px}
.field{left:466px;width:145px;height:16px;background:var(--white);border-radius:2px;font-size:6.6px;color:#555;padding:3px 6px}
.submit{left:466px;top:1142px;width:72px;height:17px}
.news-title{left:56px;top:1160px;font-size:7px;font-weight:700;color:var(--white)}
.news-input{left:56px;top:1173px;width:98px;height:14px;background:var(--white);font-size:6.4px;color:#666;padding:3px 5px}
.news-go{left:154px;top:1173px;width:20px;height:14px;font-size:7px}
.follow{left:229px;top:1160px;font-size:7px;font-weight:700;color:var(--white)}
.social{left:229px;top:1172px;display:flex;gap:5px}
.social span{width:14px;height:14px;background:#3e7a69;border-radius:2px}
.copy{left:404px;top:1182px;font-size:6.6px;color:#dfe8e5}
</style>
</head>
<body>

<div class="abs topbar"></div>
<div class="abs lang">Select Language : <span class="flag" role="img" aria-label="English flag"></span> English ▾</div>
<nav class="abs nav">
  <a class="active" href="#">Home</a><a href="#">Solutions</a><a href="#">Services</a><a href="#">PCB Products</a><a href="#">Contact</a>
</nav>

<header class="abs header"></header>
<div class="abs logo"><span class="big">RDV</span><span class="small">Harbourline Limited</span></div>
<a class="abs login" href="#">
  <svg width="10" height="8" viewBox="0 0 10 8"><rect x="0" y="1" width="10" height="6" rx="1" fill="#fff"/><circle cx="3" cy="4" r="1.3" fill="#1b5d49"/></svg>
  Member Log In</a>
<div class="abs mail">
  <svg width="11" height="8" viewBox="0 0 11 8"><rect x=".5" y=".5" width="10" height="7" fill="#fff" stroke="#0f5a3c"/><path d="M.5 .5 5.5 4.5 10.5 .5" fill="none" stroke="#0f5a3c"/></svg>
  info@rdvboard.com</div>

<section class="abs hero"></section>
<h1 class="abs hero-title">RDV Harbourline Limited strives to be a professional top notched printed circuit board supplier.</h1>
<p class="abs hero-text">We approach each customer with a long-term partnership view that delivers the lowest ownership costs and highest total values to our customers. We customize quotations and solutions in order to allow our customers to win more businesses.</p>
<a class="abs btn hero-btn" href="#">Learn more</a>
<div class="abs hero-photo" role="img" aria-label="Photo of the factory production floor with circuit board machinery"></div>
<svg class="abs slider-tab" viewBox="0 0 73 19"><path d="M0 19 8 0H65l8 19z" fill="#fff"/><circle cx="24" cy="10" r="3.5" fill="#c9cfcd"/><circle cx="36.5" cy="10" r="3.5" fill="#1d6b52"/><circle cx="49" cy="10" r="3.5" fill="#1d6b52"/></svg>

<h2 class="abs section-title principles-title">Our four excellence principles</h2>
<div class="abs principle" style="left:55px"><span class="num">1</span>Excellence in<br>Quality</div>
<div class="abs principle" style="left:202px"><span class="num">2</span>Excellence in<br>Prices</div>
<div class="abs principle" style="left:346px"><span class="num">3</span>Excellence in<br>Services</div>
<div class="abs principle" style="left:493px"><span class="num">4</span>Excellence in<br>on time delivery</div>
<div class="abs divider" style="top:411px"></div>

<h2 class="abs section-title about-title">RDV Harbourline Limited</h2>
<div class="abs about-photo" role="img" aria-label="Photo of office staff at work"></div>
<p class="abs about-text">RDV Harbourline Limited (RDV) was set up in Hong Kong in 2007 by two Hong Kong entrepreneurs, Mr. Tak Wong and Mr. Lok Fai. We acquired the single sided printed circuit board factory located in Dongguan City, Guangdong Province, China, from Tovand Corporation of the U.S. in 2007. In addition to RDV, Mr. Wong and Mr. Fai also own <b>Halberd Technology Company Limited</b>, a semiconductor company based in Hong Kong since 1997 with a total investment of over US$100 million.</p>
<p class="abs about-text full">Halberd is engaged in the manufacturing of flexible substrates &amp; assembly of <b>Micro Electro Mechanical Systems (MEMS)</b>.</p>
<a class="abs btn about-btn" href="#">Learn more</a>

<h2 class="abs section-title updates-title">Latest Chirpline updates</h2>
<div class="abs tweet" style="top:460px"><span class="avatar" role="img" aria-label="Profile photo"></span><p>We are offering single layered circuit boards by our own production in China.<br><span class="by">@ RDV Harbourline Limited, Aug 09</span></p></div>
<div class="abs tweet" style="top:505px"><span class="avatar" role="img" aria-label="Profile photo"></span><p>We are offering single layered circuit boards by our own production in China.<br><span class="by">@ RDV Harbourline Limited, Aug 09</span></p></div>
<div class="abs badge" role="img" aria-label="Follow us badge"></div>

<h2 class="abs section-title band-title products-title"><span>Products</span></h2>
<h3 class="abs prod-h" style="top:625px">Single layered printed circuit boards</h3>
<p class="abs prod-p" style="top:643px">We currently are offering single layered circuit boards through our own production facility in China for customers in the audio and video industry, home appliance and camera, industrial equipment and power supply, automotive, as well as contract manufacturers.<br><span class="more">read more...</span></p>
<div class="abs dash"></div>
<h3 class="abs prod-h" style="top:725px">Double layered and multi-layered printed circuit boards</h3>
<p class="abs prod-p" style="top:757px">We are offering two layered and multi-layered circuit boards for our customers through our strategically approved printed circuit boards manufacturers.<br><span class="more">read more...</span></p>

<h2 class="abs section-title band-title services-title"><span>Services</span></h2>
<div class="abs svc-photo" role="img" aria-label="Photo of a team meeting with customers"></div>
<p class="abs svc-text" style="top:622px">RDV is providing a RISK FREE supply of double sided and multi-layered printed circuit boards to our customers.</p>
<p class="abs svc-text" style="top:658px">With our own UL for double sided and multi-layered circuit boards, we work with a number of strategically.</p>
<p class="abs svc-text wide" style="top:699px">Our own personnel are stationed at the manufacturers' production facilities 24 hours a day 7 days a week. We provide real time update on a part number by part number basis of our customers' purchase orders status online.</p>
<p class="abs svc-text wide" style="top:741px">We examine and test 100% of boards at our own facilities before we deliver to our customers. We provide warehousing services for our customers to ensure products are delivered on a just in time basis.<br><span class="more">read more...</span></p>

<section class="abs customers"></section>
<h2 class="abs section-title customers-title">Our customers</h2>
<div class="abs cat" style="left:56px;top:864px">AutoMotive</div>
<div class="abs brands" style="left:56px;top:878px"><span><i></i>Kelwyn International</span><span>BORSK</span><span>Vantrel</span><span>Maruki Motor</span></div>
<div class="abs cat cat-rule" style="left:56px;top:905px;width:270px">Video &amp; Audio</div>
<div class="abs brands" style="left:56px;top:921px"><span>FUMARO</span><span>sorida</span></div>
<div class="abs cat cat-rule" style="left:56px;top:948px;width:270px">Contract Manufacturers</div>
<div class="abs brands" style="left:56px;top:963px"><span><i></i>Kelwyn International</span></div>
<div class="abs cat cat-rule" style="left:349px;top:864px;width:262px">Home Appliances &amp; Camera</div>
<div class="abs brands" style="left:349px;top:880px;gap:24px"><span>MITSARO</span><span>Tenrai</span><span>Shiroka</span><span>HINARO</span></div>
<div class="abs cat cat-rule" style="left:349px;top:905px;width:262px">Industrial Equipment &amp; Power Supplier</div>
<div class="abs brands" style="left:349px;top:921px"><span>ARVEN</span><span>Dalfort</span></div>

<footer class="abs footer"></footer>
<div class="abs fcol" style="left:56px"><h4>Links</h4>Solutions<br>Services<br>Why Us ?<br>Contact<br>Careers</div>
<div class="abs fcol" style="left:109px"><h4>Company</h4>About Us<br>Clients<br>Contact Us<br>Privacy Policy<br>Terms</div>
<div class="abs fcol" style="left:180px"><h4>Hong Kong Business Office</h4>RDV Harbourline Limited<br>21F Pearlview Tower<br>88 Lockhart Street<br>Wan Chai, HONG KONG<br>Telephone: (852) 2000 4417<br>Fax: (852) 2000 4418<br>Email: sales@rdvboard.com</div>
<div class="abs fcol" style="left:320px"><h4>China Factory</h4>RDV Harbourline (Dongguan) Limited<br>7 Qiaoli East Road<br>52 Industrial Zone<br>Fenggang Town, Dongguan<br>Guangdong Province, China 510990<br>Telephone: (86)769-8000 2261<br>Fax: (86)769-8000 2262</div>
<div class="abs fcol" style="left:466px"><h4>Reach us &amp; learn of our new updates</h4></div>
<div class="abs field" style="top:1049px">name</div>
<div class="abs field" style="top:1072px">email</div>
<div class="abs field" style="top:1095px">contact</div>
<div class="abs field" style="top:1118px">message</div>
<a class="abs btn submit" href="#">Submit</a>
<div class="abs news-title">SIGNUP FOR FREE NEWSLETTER</div>
<div class="abs news-input">Enter your email id</div>
<a class="abs btn news-go" href="#">OK</a>
<div class="abs follow">FOLLOW US</div>
<div class="abs social"><span role="img" aria-label="Social network link"></span><span role="img" aria-label="Social network link"></span><span role="img" aria-label="Social network link"></span></div>
<div class="abs copy">© Copyright 2012, RDV Harbourline Limited All Rights Reserved</div>

</body>
</html>
```